Verodex business card

Business card for sustainable investment company called "Verodex". Verodex is an exchange platform selling carbon credits between buyers and sellers. Carbon Credits are an environmental commodity for reducing global carbon emissions.

the card should obviously have our logo and the theme should be sustainability/environment mixed with a trading platform.

Contact Information for Business Card

Logo, Name, Title, Phone, Email

Colors
0054AA
0677BA
7BADD7
CADEEF
E8F1F8
0094D4
00A9DD
6FCCEA
C7EBF8
E9F6FB
00AB8E
00BBA5
67D7C9
C6EFE9
E9F9F6
59FF00
82FF00
B8FF75
E3FFCB
F4FFEA

```html
<!DOCTYPE html>
<html lang="en">
<head>
<meta charset="utf-8">
<title>Verodex Business Card</title>
<link href="https://fonts.googleapis.com/css2?family=Montserrat:wght@400;500;700&display=swap" rel="stylesheet">
<style>
  :root {
    --page-bg: #3a3a3a;
    --card-white: #ffffff;
    --navy: #162a52;
    --brand-blue: #0677ba;
    --accent-blue: #4a9fd4;
    --divider: #5aa5d6;
    --mark-muted: #2f5d86;
    --text-dark: #1c1c1c;
  }
  * { margin: 0; padding: 0; box-sizing: border-box; }
  html, body {
    width: 1200px; height: 1059px; overflow: hidden;
    background: var(--page-bg);
    font-family: "Montserrat", sans-serif;
  }
  .canvas { position: relative; width: 1200px; height: 1059px; }
  .card {
    position: absolute; border-radius: 22px; overflow: hidden;
    box-shadow: 0 14px 24px rgba(0,0,0,0.45);
  }
  .card-front { left: 256px; top: 100px; width: 688px; height: 391px; background: var(--card-white); }
  .card-back { left: 253px; top: 537px; width: 694px; height: 394px; background: var(--navy); }

  .brand { position: absolute; display: flex; align-items: center; }
  .brand-square { display: block; flex: none; background: var(--brand-blue); }
  .brand-name { font-weight: 700; letter-spacing: 0.5px; line-height: 1; }

  .front-brand { left: 69px; top: 196px; transform: translateY(-50%); gap: 14px; }
  .front-brand .brand-square { width: 40px; height: 40px; }
  .front-brand .brand-name { font-size: 36px; color: var(--navy); }

  .divider { position: absolute; left: 343px; top: 126px; width: 2px; height: 139px; background: var(--divider); }

  .person { position: absolute; left: 375px; top: 127px; }
  .person-name { font-size: 27px; font-weight: 700; color: var(--navy); letter-spacing: 0.6px; line-height: 1; }
  .person-title { font-size: 18px; font-weight: 500; color: var(--navy); letter-spacing: 0.5px; margin-top: 4px; }

  .contacts { position: absolute; left: 374px; top: 192px; list-style: none; }
  .contacts li {
    display: flex; align-items: center; gap: 8px;
    font-size: 16px; color: var(--text-dark); height: 26px; letter-spacing: 0.3px;
  }
  .contacts svg { width: 13px; height: 13px; flex: none; }

  .address-band {
    position: absolute; left: 0; top: 315px; width: 100%; height: 24px;
    background: var(--navy); color: #fff; font-size: 15px; font-weight: 500;
    display: flex; align-items: center; justify-content: center; letter-spacing: 0.4px;
  }

  .back-brand { left: 50%; top: 50%; transform: translate(-50%, -50%); gap: 26px; }
  .back-brand .brand-square { width: 78px; height: 78px; background: var(--mark-muted); }
  .back-brand .brand-name { font-size: 62px; color: var(--mark-muted); }
</style>
</head>
<body>
<div class="canvas">
  <section class="card card-front">
    <div class="brand front-brand">
      <span class="brand-square"></span>
      <span class="brand-name">VERODEX</span>
    </div>
    <div class="divider"></div>
    <div class="person">
      <p class="person-name">DANIEL REYES</p>
      <p class="person-title">MANAGER</p>
    </div>
    <ul class="contacts">
      <li>
        <svg viewBox="0 0 24 24"><path fill="var(--accent-blue)" d="M6.6 10.8a15 15 0 0 0 6.6 6.6l2.2-2.2c.3-.3.7-.4 1-.2 1.1.4 2.3.6 3.6.6.6 0 1 .4 1 1V20c0 .6-.4 1-1 1A17 17 0 0 1 3 4c0-.6.4-1 1-1h3.5c.6 0 1 .4 1 1 0 1.3.2 2.5.6 3.6.1.3 0 .7-.2 1z"/></svg>
        555-210-4836
      </li>
      <li>
        <svg viewBox="0 0 24 24"><rect x="2" y="5" width="20" height="14" rx="2" fill="var(--accent-blue)"/><path d="M3 6l9 7 9-7" stroke="#fff" stroke-width="1.8" fill="none"/></svg>
        hello@verodex.com
      </li>
      <li>
        <svg viewBox="0 0 24 24" fill="none" stroke="var(--accent-blue)" stroke-width="1.8"><circle cx="12" cy="12" r="10"/><ellipse cx="12" cy="12" rx="4.5" ry="10"/><path d="M2 12h20M4 7h16M4 17h16"/></svg>
        www.verodex.com
      </li>
    </ul>
    <div class="address-band">2217 Harbor Lane Suite 40 Fairview, OR 97024</div>
  </section>

  <section class="card card-back">
    <div class="brand back-brand">
      <span class="brand-square"></span>
      <span class="brand-name">VERODEX</span>
    </div>
  </section>
</div>
</body>
</html>
```